Modern Business Card for Larkwell 2018

Our company assumes the best about people. We are creating an online community of entrepreneurs and business leaders who struggle with marketing their business online.

This business card should POP! We recently got a new logo and are launching a new website next month, so our business cards should make a statement that feels:
-Fresh
-Smart
-Trustworthy
-Fun

Target Market(s)

small business owners, entrepreneurs

Industry/Entity Type

Digital Marketing

Contact Information for Business Card

Dimensions: 3.5" x 2"

Font styles to use
Sans Serif

Colors
f37122
ffffff

Requirements
Must have
• We need a business card with a modern, bold design. We will use one side of the card as a lead-generation offer, so text on one side will need to fit up to 140 characters. The business card should stick to our core colors (orange, black, and white).
Nice to have
• We think a vertical "portrait" design could be interesting.
Should not have
• Should not look like a traditional business card. The round icon should stand out from a distance.

```html
<!DOCTYPE html>
<html lang="en">
<head>
<meta charset="utf-8">
<title>Larkwell Business Card</title>
<link rel="stylesheet" href="https://fonts.googleapis.com/css2?family=Roboto:wght@400;500;700&family=Alex+Brush&display=swap">
<style>
  :root {
    --orange: #f37122;
    --white: #ffffff;
    --card: #f4f4f4;
    --ink: #1f1f1f;
    --rule: #8a8a8a;
    --backdrop: #dcdcdc;
  }
  * { margin: 0; padding: 0; box-sizing: border-box; }
  html, body { width: 1200px; height: 960px; overflow: hidden; }
  body { background: var(--backdrop); font-family: "Roboto", Arial, sans-serif; }
  .canvas { position: relative; width: 1200px; height: 960px; }
  .card {
    position: absolute;
    width: 343px;
    height: 598px;
    background: var(--card);
    box-shadow: 0 2px 4px rgba(0,0,0,0.25);
    overflow: hidden;
  }
  .card--front { left: 249px; top: 180px; }
  .card--back { left: 608px; top: 182px; }

  .person-name {
    position: absolute;
    left: 171px; top: 236px;
    transform: translate(-50%, -50%) rotate(-90deg);
    white-space: nowrap;
    font-family: "Alex Brush", cursive;
    font-size: 58px;
    color: var(--orange);
  }
  .person-role {
    position: absolute; left: 0; right: 0; top: 434px;
    text-align: center; font-weight: 500; font-size: 20px; color: var(--ink);
  }
  .person-email {
    position: absolute; left: 0; right: 0; top: 459px;
    text-align: center; font-size: 15px; color: var(--ink);
  }
  .brand-mark {
    position: absolute; left: 0; right: 0;
    display: flex; flex-direction: column; align-items: center;
  }
  .brand-dot { width: 40px; height: 40px; border-radius: 50%; background: var(--orange); }
  .card--front .brand-mark { top: 494px; }
  .card--front .brand-name { margin-top: 6px; font-weight: 700; font-size: 14px; letter-spacing: 2px; color: var(--orange); }

  .card--back .brand-mark { top: 42px; }
  .card--back .brand-name { margin-top: 12px; font-weight: 700; font-size: 40px; letter-spacing: 1px; color: var(--ink); line-height: 1; }
  .tagline {
    position: absolute; left: 0; right: 0; top: 139px;
    text-align: center; font-weight: 500; font-size: 12px; letter-spacing: 1px; color: var(--ink);
  }
  .write-lines { position: absolute; left: 44px; top: 221px; width: 253px; }
  .write-line { height: 2px; background: var(--rule); margin-bottom: 36px; }
  .offer {
    position: absolute; left: 34px; top: 375px; width: 272px; height: 230px;
    background: var(--orange); border-radius: 14px 14px 0 0;
    color: var(--white); text-align: center; padding-top: 26px;
  }
  .offer-headline { font-weight: 700; font-size: 20.5px; line-height: 24px; }
  .offer-text { margin-top: 6px; font-size: 14px; line-height: 18px; }
  .offer-link { margin-top: 14px; font-weight: 700; font-size: 19px; }
</style>
</head>
<body>
<main class="canvas">
  <section class="card card--front">
    <p class="person-name">Dana Whitfield</p>
    <p class="person-role">STORY MARKETING COACH</p>
    <p class="person-email">dana@larkwellnow.com</p>
    <div class="brand-mark">
      <span class="brand-dot"></span>
      <span class="brand-name">LARKWELL</span>
    </div>
  </section>

  <section class="card card--back">
    <div class="brand-mark">
      <span class="brand-dot"></span>
      <span class="brand-name">LARKWELL</span>
    </div>
    <p class="tagline">SHARE IDEAS THAT SPARK GROWTH</p>
    <div class="write-lines">
      <div class="write-line"></div>
      <div class="write-line"></div>
      <div class="write-line"></div>
      <div class="write-line"></div>
    </div>
    <div class="offer">
      <p class="offer-headline">REACH MORE PEOPLE.<br>MAKE MORE MONEY.<br>CREATE MORE IMPACT.</p>
      <p class="offer-text">Get your free Larkwell<br>Starter Package and our<br>marketing guide today at</p>
      <p class="offer-link">Larkwellnow.com/start</p>
    </div>
  </section>
</main>
</body>
</html>
```